Label Design for Climbing Chalk (fitness category)

I am looking for someone to design a front and back label for a bottle of liquid chalk. Liquid chalk is used in gyms, gymnastics, climbing to prevent your hands from getting moist and increase friction. I'm uploading some design motivations that I like.

The bottle is going to be black and I want the label to be clear. You have free reign of how you want to approach this design. Below are more specifics for the sizing:

*Attached is a picture of a competitor product (Tor Hold Liquid Chalk). Please don't use this for motivation, their label is very bad. I'm attaching a picture so that you can see what the bottle looks like.
*Attached are design motivations that I like
*The bottle is 50 ml, it's 3.75 inches tall, 2 inches wide and 1.25 inches in depth.
*The label can be square or oval (it's up to you). The size of the label needs to be 1,25 x 2.25 inches.
*Name of the product: Bravan Liquid Chalk
*Label needs to have the following Required Text. You can arrange it however you like:
- (50 ml)
- Made by USA Competitive Athletes for Athletes. Increases grip and lasts 3-4 times longer than regular chalk.
- Directions: Shake well. Squeeze some Bravan Liquid Chalk into your hand and rub your hands together. Let your hands air dry for about 10 seconds. To remove the chalk wash your hands with light soap.
Warning: Avoid contact with Eyes. Do not use on broken skin. Do not ingest. Keep out of reach of small children.
- Ingredients: Magnesium carbonate, SD Alcohol, hydroxypropylcellulose, colophonium.

Target Market(s)

Fitness, Athletes, Rock Climbers, Weight Lifters, Gymnasts, etc

Industry/Entity Type

Fitness

Font styles to use
Sans Serif

Colors

Designer to choose colors to be used in the design.

Requirements
Must have
• Please see Project Description for required text. The bottle is going to be black and I want the clear label so please be creative with the colors that would look good
Nice to have
• Please see attached branding ideas that I liked for font and colors. You don't have to strictly stick to them, these are just some of the ones I liked. Be creative and put your best foot forward.

```html
<!DOCTYPE html>
<html lang="en">
<head>
<meta charset="utf-8">
<title>Bravan Liquid Chalk – Front and Back Labels</title>
<link rel="stylesheet" href="https://fonts.googleapis.com/css2?family=Montserrat:ital,wght@0,400;0,500;1,400;1,700&family=Oswald:wght@700&display=swap">
<style>
  :root {
    --teal: #0b5f6f;
    --teal-deep: #03586a;
    --teal-soft: #7fa7b0;
    --paper: #f1f1f1;
    --white: #ffffff;
    --ink: #111111;
    --alert-red: #c0252c;
  }
  html, body {
    margin: 0;
    padding: 0;
    width: 1200px;
    height: 1029px;
    overflow: hidden;
    background: var(--white);
  }
  .label-sheet { display: block; width: 1200px; height: 1029px; }
  .label-edge { fill: var(--white); }
  .label-ring { fill: var(--teal); }
  .front-face { fill: var(--paper); }
  .back-face { fill: var(--white); }
  .deep-fill { fill: var(--teal-deep); }
  .art-area { fill: url(#art-tone); }
  .brand-name {
    font-family: "Oswald", "Arial Narrow", sans-serif;
    font-weight: 700;
    fill: var(--teal);
    text-anchor: middle;
    letter-spacing: 1px;
  }
  .product-title {
    font-family: "Oswald", "Arial Narrow", sans-serif;
    font-weight: 700;
    fill: var(--ink);
    text-anchor: middle;
  }
  .claim-text {
    font-family: "Montserrat", Arial, sans-serif;
    font-style: italic;
    font-size: 21px;
    letter-spacing: 1.2px;
    fill: var(--white);
    text-anchor: middle;
  }
  .volume {
    font-family: "Montserrat", Arial, sans-serif;
    font-weight: 500;
    font-size: 31px;
    fill: var(--teal);
    text-anchor: middle;
  }
  .section-head {
    font-family: "Montserrat", Arial, sans-serif;
    font-style: italic;
    font-weight: 700;
    font-size: 21px;
    fill: var(--alert-red);
  }
  .body-copy {
    font-family: "Montserrat", Arial, sans-serif;
    font-size: 16.5px;
    letter-spacing: 0.6px;
    fill: var(--ink);
  }
  .ingredients-head {
    font-family: "Montserrat", Arial, sans-serif;
    font-style: italic;
    font-weight: 700;
    font-size: 18px;
    fill: var(--ink);
    text-anchor: middle;
  }
  .ingredients-list {
    font-family: "Montserrat", Arial, sans-serif;
    font-style: italic;
    font-size: 17px;
    fill: var(--ink);
    text-anchor: middle;
  }
</style>
</head>
<body>
<svg class="label-sheet" viewBox="0 0 1200 1029" xmlns="http://www.w3.org/2000/svg">
  <defs>
    <filter id="label-shadow" x="-20%" y="-10%" width="150%" height="130%">
      <feDropShadow dx="14" dy="28" stdDeviation="16" flood-color="#000" flood-opacity="0.35"/>
    </filter>
    <linearGradient id="art-tone" x1="0" y1="0" x2="0" y2="1">
      <stop offset="0" stop-color="#03586a"/>
      <stop offset="1" stop-color="#7fa7b0"/>
    </linearGradient>
    <clipPath id="front-window">
      <rect x="183" y="164" width="367" height="710" rx="183"/>
    </clipPath>
  </defs>

  <!-- Front label -->
  <g class="front-label">
    <rect class="label-edge" x="146" y="126" width="440" height="786" rx="220" filter="url(#label-shadow)"/>
    <rect class="label-ring" x="154" y="134" width="424" height="770" rx="212"/>
    <rect class="front-face" x="183" y="164" width="367" height="710" rx="183"/>

    <g clip-path="url(#front-window)">
      <rect class="art-area" role="img" aria-label="Illustration area: climber on a rock overhang"
            x="312" y="164" width="240" height="120"/>
      <rect class="art-area" role="img" aria-label="Illustration area: mountain ridge"
            x="176" y="590" width="380" height="28"/>
      <rect class="deep-fill" x="176" y="616" width="380" height="160"/>
    </g>

    <text class="brand-name" x="366" y="410" font-size="96">Bravan</text>

    <text class="product-title" x="364" y="496" font-size="72">LIQUID</text>
    <text class="product-title" x="364" y="566" font-size="72">CHALK</text>

    <text class="claim-text" x="364" y="658">Made by USA Competitive</text>
    <text class="claim-text" x="364" y="682">Athletes for Athletes.</text>
    <text class="claim-text" x="362" y="706">Increases grip and lasts</text>
    <text class="claim-text" x="360" y="730">3-4 times longer than</text>
    <text class="claim-text" x="350" y="754">regular chalk.</text>

    <text class="volume" x="366" y="842">50 ml</text>
  </g>

  <!-- Back label -->
  <g class="back-label">
    <rect class="label-edge" x="666" y="126" width="440" height="786" rx="220" filter="url(#label-shadow)"/>
    <rect class="label-ring" x="676" y="134" width="420" height="770" rx="210"/>
    <rect class="back-face" x="704" y="164" width="364" height="710" rx="182"/>

    <rect class="art-area" role="img" aria-label="Illustration area: small climber emblem"
          x="840" y="174" width="96" height="58" rx="6"/>
    <text class="brand-name" x="880" y="278" font-size="44">Bravan</text>

    <text class="product-title" x="880" y="316" font-size="38">LIQUID</text>
    <text class="product-title" x="880" y="350" font-size="38">CHALK</text>

    <text class="section-head" x="720" y="388">Directions:</text>
    <text class="body-copy" x="720" y="412" textLength="332" lengthAdjust="spacing">Shake well. Squeeze some Bravan</text>
    <text class="body-copy" x="720" y="436" textLength="332" lengthAdjust="spacing">Liquid Chalk into your hand and rub</text>
    <text class="body-copy" x="720" y="460" textLength="332" lengthAdjust="spacing">your hands together. Let your hands</text>
    <text class="body-copy" x="720" y="484" textLength="332" lengthAdjust="spacing">air dry for about 10 seconds. To</text>
    <text class="body-copy" x="720" y="508" textLength="332" lengthAdjust="spacing">remove the chalk wash your hands</text>
    <text class="body-copy" x="720" y="532">with light soap.</text>

    <text class="section-head" x="720" y="574">Warning:</text>
    <text class="body-copy" x="720" y="599" textLength="332" lengthAdjust="spacing">Avoid contact with Eyes. Do not use</text>
    <text class="body-copy" x="720" y="623" textLength="332" lengthAdjust="spacing">on broken skin. Do not ingest. Keep</text>
    <text class="body-copy" x="720" y="647">out of reach of small children.</text>

    <rect class="label-ring" x="749" y="682" width="273" height="9"/>

    <text class="ingredients-head" x="884" y="734">Ingredients:</text>
    <text class="ingredients-list" x="884" y="758">Magnesium carbonate, SD Alcohol,</text>
    <text class="ingredients-list" x="884" y="782">hydroxypropylcellulose,</text>
    <text class="ingredients-list" x="884" y="806">colophonium.</text>
  </g>
</svg>
</body>
</html>
```